San Francisco Leading Consulting firm - 47Vora Web Design Project

•Create a Web Design
•Uncoded webpage layout design
•2 Pages Design - Homepage + Interior Page

Task Description
Hello, we're looking for a re-design our current website www.47vora-example.com

we have a sample mockup design @

http://47vora.pubtrellis-example.org/

This shows the layout that we like and also a sample of 6 pictures that would change based on where you mouse over..

6 pictures HOME design needs to be included.

SMART
THOUGHTFUL
FLEXIBLE
CREATIVE SERVICES
TECHNICAL SERVICES
PARTNERS

sites we like:

http://www.melvanadvisory-example.com/Home.cfm?id=Home
http://www.plinthworks-example.com/index.html

Our company can be best described as: 100+ employees, cutting-edge, depandable, innovative, strong, smart.

Our Primary focus is: IT Consulting Services and Creative Design services

47Vora LLC is a consulting firm providing creative design, business and technology solutions to both private and public interests.

Established in 1996, 47Vora is a San Francisco based company providing specialists for a range of business needs including:

Creative Design Services
•Print
•Logo Design
•Website Design
•Illustration

and

Business and Technology solutions

•Application Software and Web Development
•Business Process Re-Design (BPR)
•Business/Systems Analysis and Requirement Documentation
•Mentoring and Training
•Network/Hardware Installation Services
•System Design and Architecture
•Vendor Management
•Docuvault Architecture and Implementation

our sample mockup site:

Reason: Due to holiday season, we're not available to work with designers and finilize our design.  

Thank you very much for submitting your design.

We appreciate your time and creativity.   Since, our office is currently closed for holidays, we will be reviewing it in details next week and will make our decision as soon as possible.

It would be great if you could submit any of your changes by Wed next week, so it would be part of our reviews. 

Please see updated wireframe under attachments:  we have some minor updates to our wireframe that we would like you to update your designs, if possible.  

We also encorouge you not to use our standard wireframe and come up with more unique designs.   Everything would be considered when we review your design.

 

Target Market(s)

Creative services and professional services clients, including government agencies

Industry/Entity Type

Business

Requirements
Must have
• Clean, professional look, easy navigation

```html
<!DOCTYPE html>
<html lang="en">
<head>
<meta charset="utf-8">
<title>47Vora — Company Overview</title>
<link rel="stylesheet" href="https://fonts.googleapis.com/css2?family=Arimo:wght@400;700&display=swap">
<style>
  :root {
    --blue: #0a8ec4;
    --blue-deep: #0a7fb3;
    --text: #3d3d3d;
    --text-soft: #707070;
    --heading: #222;
    --rule: #c9c9c9;
    --frame: #8a8a8a;
    --white: #fff;
  }
  * { margin: 0; padding: 0; box-sizing: border-box; }
  html, body { width: 1200px; height: 900px; overflow: hidden; background: var(--white); }
  body { position: relative; font-family: "Arimo", Helvetica, Arial, sans-serif; color: var(--text); }
  .abs { position: absolute; }

  /* Header */
  .brand { left: 136px; top: 22px; display: flex; align-items: center; gap: 10px; }
  .brand-dot { width: 28px; height: 28px; border-radius: 50%; background: var(--blue); }
  .brand-name { font-size: 30px; font-weight: 400; color: #6d6d6d; letter-spacing: 1px; }

  .main-nav { left: 340px; top: 38px; display: flex; font-size: 15px; }
  .main-nav a { color: #555; text-decoration: none; padding: 0 12px; border-left: 1px solid var(--blue); line-height: 18px; }
  .main-nav a:first-child { border-left: none; }
  .main-nav a.is-current { color: var(--blue); }

  .contact { left: 929px; top: 12px; font-size: 12px; line-height: 18px; color: #222; }
  .contact strong { color: var(--blue); font-weight: 700; display: block; }

  /* Banner */
  .hero { left: 121px; top: 100px; width: 961px; height: 201px; border-radius: 8px;
    background:
      linear-gradient(170deg, rgba(120,190,215,.55) 0%, rgba(120,190,215,0) 40%),
      linear-gradient(180deg, #cfd3d6 0%, #9ea4a8 45%, #6f767b 100%); }

  /* Overview */
  .overview-panel { left: 130px; top: 317px; width: 580px; height: 175px; border-radius: 0 10px 0 0;
    background: linear-gradient(100deg, rgba(255,255,255,0) 30%, #e6e6e6 100%),
                linear-gradient(180deg, #ececec 0%, rgba(255,255,255,0) 100%); }
  .chevron { width: 22px; height: 36px; }
  .overview-chevron { left: 122px; top: 338px; }
  .overview-title { left: 158px; top: 336px; font-size: 37px; font-weight: 400; color: var(--heading); }
  .overview-lede { left: 124px; top: 391px; width: 480px; font-size: 20px; line-height: 24px; color: var(--blue); }
  .overview-body { left: 119px; top: 476px; width: 520px; font-size: 14px; line-height: 24px; color: var(--text); }
  .overview-intro { left: 119px; top: 619px; width: 500px; font-size: 14px; line-height: 24px; font-weight: 700; color: var(--text); }

  /* Sidebar */
  .featured-label { left: 743px; top: 333px; font-size: 16px; font-weight: 700; line-height: 20px; color: #222; }
  .featured-chevron { left: 825px; top: 333px; }
  .client { top: 340px; font-size: 14px; font-weight: 700; color: #333; }
  .view-work { left: 957px; top: 383px; font-size: 14px; font-weight: 700; color: var(--blue); }
  .service-btn { left: 775px; width: 300px; height: 27px; border-radius: 8px; background: var(--blue-deep);
    color: var(--white); font-size: 17px; line-height: 27px; padding: 0 12px 0 7px; display: flex; justify-content: space-between; }
  .service-btn b { font-weight: 700; font-size: 20px; }
  .partners-card { left: 775px; top: 520px; width: 300px; height: 130px; border: 1px solid var(--frame); border-radius: 4px; overflow: hidden; }
  .partners-card h3 { position: absolute; left: 7px; top: 6px; font-size: 17px; font-weight: 400; color: #222; }
  .partners-visual { position: absolute; left: 75px; top: 4px; width: 160px; height: 122px; border-radius: 50%;
    background: radial-gradient(circle at 50% 50%, #2d74c9 0%, #58b6e6 45%, rgba(200,235,250,.6) 70%, rgba(255,255,255,0) 72%); }
  .partners-corner { position: absolute; right: 0; bottom: 0; }

  /* Services list */
  .services { left: 124px; top: 685px; width: 955px; height: 122px; border: 1px solid var(--frame); border-radius: 10px;
    display: grid; grid-template-columns: 324px 324px 1fr; padding: 12px 0 0 16px; }
  .services ul { list-style: none; font-size: 15px; line-height: 24px; color: var(--text-soft); }

  /* Footer */
  .footer-rule { left: 120px; top: 830px; width: 960px; height: 1px; background: var(--rule); }
  .copyright { left: 132px; top: 856px; font-size: 12px; color: #333; }
  .footer-nav { left: 543px; top: 856px; font-size: 12px; display: flex; gap: 30px; }
  .footer-nav a { color: var(--blue); text-decoration: none; }
</style>
</head>
<body>
  <header>
    <div class="abs brand"><span class="brand-dot"></span><span class="brand-name">47VORA</span></div>
    <nav class="abs main-nav">
      <a class="is-current" href="#">Company</a><a href="#">Creative Services</a><a href="#">Technical Services</a><a href="#">Partners</a><a href="#">Contact Us</a>
    </nav>
    <address class="abs contact" style="font-style:normal">
      2275 Harbor Row, Ste 410<br>San Francisco, CA 94105
      <strong>415-555-0147</strong><strong>info@47vora-example.com</strong>
    </address>
  </header>

  <div class="abs hero" role="img" aria-label="Black and white San Francisco skyline with a translucent blue arc"></div>

  <main>
    <div class="abs overview-panel"></div>
    <svg class="abs chevron overview-chevron" viewBox="0 0 22 36"><path d="M2 0h8l12 18-12 18H2l12-18z" fill="var(--blue)"/></svg>
    <h1 class="abs overview-title">Company Overview</h1>
    <p class="abs overview-lede">47Vora provides professional experience in all phases of IT projects from vendor selection to post production support.</p>
    <p class="abs overview-body">&nbsp;We assist our clients not only in their IT solutions, but also provide professional services such as transitioning with conversion activities, Business Process Reengineering (BPR), training and business support. We have provided vendor analysis and selection, project oversight, architecture, requirements gathering and system certification functions.</p>
    <p class="abs overview-intro">Our corporate consulting services include a wide array of talent and expertise in the following:</p>

    <aside>
      <p class="abs featured-label">Featured<br>Clients</p>
      <svg class="abs chevron featured-chevron" viewBox="0 0 22 36"><path d="M2 0h8l12 18-12 18H2l12-18z" fill="var(--blue)"/></svg>
      <span class="abs client" style="left:864px">Kestrel</span>
      <span class="abs client" style="left:930px">Orbitline</span>
      <span class="abs client" style="left:1012px">Tallwave</span>
      <a class="abs view-work" href="#">+&nbsp; View Our Work</a>

      <div class="abs service-btn" style="top:431px">Business &amp; Technical Services<b>+</b></div>
      <div class="abs service-btn" style="top:469px">Creative Services<b>+</b></div>

      <div class="abs partners-card">
        <div class="partners-visual" role="img" aria-label="Glowing blue globe with network lines"></div>
        <h3>Partners</h3>
        <svg class="partners-corner" width="50" height="50" viewBox="0 0 50 50">
          <path d="M50 0V50H0z" fill="var(--blue-deep)"/>
          <path d="M37 28v14M30 35h14" stroke="#fff" stroke-width="2.5"/>
        </svg>
      </div>
    </aside>

    <section class="abs services">
      <ul><li>Application Software and Web Development</li><li>Business Process Re-Design (BPR)</li><li>Systems Analysis and Requirement Docs</li><li>Mentoring and Training</li></ul>
      <ul><li>Network/Hardware Installation Services</li><li>System Design and Architecture</li><li>Vendor Management</li><li>Docuvault Architecture and Implementation</li></ul>
      <ul><li>Print &amp; Package Design</li><li>Brand and Identity Creation</li><li>Website and User Experience Design</li><li>Illustration Design</li></ul>
    </section>
  </main>

  <footer>
    <div class="abs footer-rule"></div>
    <p class="abs copyright">Copyright 2011, 47Vora, LLC All rights reserved.</p>
    <nav class="abs footer-nav">
      <a href="#">Home</a><a href="#">Company</a><a href="#">Technical Services</a><a href="#">Creative Services</a><a href="#">Partners</a><a href="#">Contact Us</a>
    </nav>
  </footer>
</body>
</html>
```